Larkfield Ridge Management

I need a professional website. My current website is larkfieldridgemanagement.com and I hate it. It was created with some AI tool very quickly because I needed a site up and running with no advanced notice. I’m open to all designs .. I trust you, the professionals will deliver the results I’m anxiously awaiting! :)

```html
<!DOCTYPE html>
<html lang="en">
<head>
<meta charset="utf-8">
<title>Larkfield Ridge Management</title>
<link href="https://fonts.googleapis.com/css2?family=Poppins:wght@400;500;600&display=swap" rel="stylesheet">
<style>
:root{--navy:#243a5e;--red:#d22b2b;--grey:#f0f0f0;--card:#585858;--ink:#222;--muted:#666;--white:#fff;}
*{box-sizing:border-box;margin:0;padding:0}
html,body{width:1200px;height:5072px;overflow:hidden}
body{font-family:"Poppins",sans-serif;color:var(--ink);background:var(--white);position:relative}
.abs{position:absolute}
.btn{display:inline-flex;height:40px}
.btn span{background:var(--red);color:#fff;font-size:11px;font-weight:500;display:flex;align-items:center;padding:0 20px}
.btn i{width:40px;margin-left:3px;background:var(--red);display:flex;align-items:center;justify-content:center}
.btn.light span{background:#fff;color:var(--navy)}
.btn.light i{background:#fff}
.eyebrow{color:var(--red);font-size:11px;text-transform:uppercase}
.h2{font-size:32px;font-weight:500;line-height:1.2}
.center{text-align:center;width:1200px;left:0}
.photo{position:absolute}
/* hero */
.hero{top:0;left:0;width:1200px;height:674px;background:linear-gradient(180deg,#5b7fb8 0%,#a99bb5 30%,#d7a08a 48%,#4a5a3c 75%,#2e3a24 100%)}
.nav{top:34px;left:93px;display:flex;gap:34px;font-size:12px;color:#fff}
.nav .active{color:var(--red)}
.brand{top:18px;left:530px;width:140px;text-align:center;color:#fff;font-weight:600;font-size:15px;line-height:1.2}
.brand b{display:block;width:22px;height:22px;border-radius:50%;background:var(--red);margin:0 auto 6px}
.hero h1{top:120px;font-size:48px;font-weight:600;color:#fff;line-height:1.15}
.hero p{top:240px;font-size:12px;color:#fff;line-height:1.5}
.notch{left:570px;top:644px;width:0;height:0;border-left:30px solid transparent;border-right:30px solid transparent;border-bottom:30px solid #fff}
/* features */
.feat{top:710px;left:93px;display:flex;gap:8px}
.feat div{width:198px;height:130px;border:1px solid #ddd;position:relative;text-align:center;font-size:12px;padding-top:36px;line-height:1.4}
.feat div:after{content:"";position:absolute;right:0;bottom:0;border-left:12px solid transparent;border-bottom:12px solid var(--red)}
.feat svg{display:block;margin:0 auto 8px}
/* about */
.about{top:906px;left:93px;width:1018px;height:428px;background:var(--navy);color:#fff}
.about .h2{color:#fff}
/* services */
.services{top:1399px;left:0;width:1200px;height:646px;background:var(--grey)}
.svc{top:148px;height:362px;color:#fff}
.svc h3{position:absolute;left:22px;bottom:26px;font-size:20px;font-weight:500}
.arrow{width:38px;height:38px;border-radius:50%;border:1px solid #999;display:flex;align-items:center;justify-content:center;background:#fff}
/* why */
.why{top:2108px;left:97px;width:1013px;height:454px;border:4px solid var(--navy);background:linear-gradient(100deg,#8ba0b4,#c9cfc9 50%,#7f8f6c)}
.why .panel{left:60px;top:36px;width:380px;height:374px;background:#fff;padding:38px 28px}
.why li{list-style:none;font-size:13px;margin:12px 0;padding-left:18px;position:relative}
.why li:before{content:"";position:absolute;left:0;top:6px;width:7px;height:7px;border-radius:50%;background:var(--red)}
/* faq */
.faq{top:3388px;left:91px;width:1004px;height:454px;background:var(--navy)}
.q{left:24px;width:390px;height:38px;border:1px solid #5a6d8c;color:#fff;font-size:13px;display:flex;align-items:center;justify-content:space-between;padding:0 14px 0 30px}
.q:before{content:"";position:absolute;left:14px;width:6px;height:6px;border-radius:50%;background:#fff}
/* reviews */
.rev{top:3985px;width:332px;height:211px;background:var(--card);color:#fff;padding:26px;border-bottom:3px solid var(--red)}
.rev .who{display:flex;gap:12px;align-items:center;font-size:13px}
.rev .av{width:38px;height:38px;border-radius:50%;background:#999}
.rev .st{color:var(--red);font-size:12px;letter-spacing:2px}
.rev p{font-size:11px;line-height:1.65;margin-top:18px}
/* footer */
.foot h4{font-size:14px;font-weight:500;margin-bottom:18px}
.foot li{list-style:none;font-size:10px;color:var(--muted);margin-bottom:8px}
</style>
</head>
<body>

<header class="hero abs" role="img" aria-label="Two-storey family home with lit windows at sunset, lawn and trees">
  <nav class="nav abs"><span class="active">Home</span><span>About Us ⌄</span><span>Services ⌄</span><span>Resources</span><span>FAQs</span></nav>
  <div class="brand abs"><b></b>LARKFIELD<br>RIDGE</div>
  <div class="abs" style="top:26px;left:898px;display:flex;gap:8px">
    <div class="btn" style="height:34px"><span>Contact Us</span><i style="width:34px">★</i></div>
    <div style="width:56px;height:34px;border:1px solid #fff;color:#fff;font-size:11px;display:flex;align-items:center;justify-content:center">EN ⌄</div>
  </div>
  <h1 class="abs center">Reliable Property<br>Management Solutions</h1>
  <p class="abs center">Larkfield Ridge Management LLC helps property owners protect their investments<br>while creating better experiences for tenants.</p>
  <div class="btn abs" style="top:295px;left:490px"><span>Explore Our Services</span><i style="color:#fff">★</i></div>
  <div class="notch abs"></div>
</header>

<section class="feat abs">
  <div><svg width="26" height="26" viewBox="0 0 26 26"><circle cx="13" cy="13" r="10" fill="none" stroke="#d22b2b" stroke-width="2"/><circle cx="13" cy="13" r="4" fill="#d22b2b"/></svg>Data-Driven<br>Property Management</div>
  <div><svg width="26" height="26" viewBox="0 0 26 26"><path d="M3 13 13 4l10 9v10H3z" fill="none" stroke="#d22b2b" stroke-width="2"/></svg>Professional<br>Tenant Services</div>
  <div><svg width="26" height="26" viewBox="0 0 26 26"><circle cx="13" cy="13" r="10" fill="none" stroke="#d22b2b" stroke-width="2"/><path d="M13 5v16M5 13h16" stroke="#d22b2b" stroke-width="2"/></svg>Asset<br>Preservation Focus</div>
  <div><svg width="26" height="26" viewBox="0 0 26 26"><rect x="3" y="5" width="20" height="14" rx="7" fill="none" stroke="#d22b2b" stroke-width="2"/></svg>Transparent<br>Communication</div>
  <div><svg width="26" height="26" viewBox="0 0 26 26"><path d="M13 3 22 7v6c0 6-4 9-9 11-5-2-9-5-9-11V7z" fill="none" stroke="#d22b2b" stroke-width="2"/></svg>Reliable Maintenance<br>Coordination</div>
</section>

<section class="about abs">
  <div class="photo" role="img" aria-label="Handshake over a desk beside a small model house" style="left:8px;top:8px;width:566px;height:412px;background:linear-gradient(135deg,#9b4a3a,#d8cfc4 55%,#7a6a5a)"></div>
  <div class="abs" style="left:630px;top:44px;width:360px">
    <div class="eyebrow">About Us</div>
    <div class="h2" style="margin-top:10px">Your Trusted Partner in Property Management</div>
    <p style="font-size:10px;line-height:1.8;margin-top:16px">Larkfield Ridge Management LLC is a real estate and property management firm. Our organization delivers comprehensive property management solutions that optimize asset performance and tenant satisfaction. By integrating advanced analytics with proven operational frameworks, our specialists ensure each property achieves sustained value appreciation.</p>
    <p style="font-size:10px;line-height:1.8;margin-top:14px">Drawing on decades of collective expertise, the team facilitates regulatory compliance, cost efficiency, and proactive maintenance.</p>
    <div class="btn" style="margin-top:22px"><span>Learn More About Us</span><i style="color:#fff">★</i></div>
  </div>
</section>

<section class="services abs">
  <div class="abs center eyebrow" style="top:66px">Services</div>
  <div class="abs center h2" style="top:84px">Complete Property Management Solutions</div>
  <div class="arrow abs" style="left:38px;top:303px">←</div>
  <div class="svc photo" role="img" aria-label="Model house with keys on a table" style="left:93px;width:366px;background:linear-gradient(160deg,#e6e6e6,#a34030 55%,#2a3e62);border:4px solid var(--navy)">
    <div class="abs" style="left:0;right:0;bottom:0;height:92px;background:var(--navy)"></div>
    <h3 style="bottom:50px">Property Management</h3>
    <p class="abs" style="left:22px;bottom:20px;font-size:10px;width:320px;line-height:1.5">Comprehensive day-to-day management that protects your investment while delivering exceptional service to tenants.</p>
  </div>
  <div class="svc photo" role="img" aria-label="Agent handing documents to a tenant at a front door" style="left:467px;width:366px;background:linear-gradient(160deg,#6a4a3a,#b8a898 50%,#3a3a4a)"><h3>Tenant Placement</h3></div>
  <div class="svc photo" role="img" aria-label="Colleagues reviewing financial charts" style="left:841px;width:359px;background:linear-gradient(160deg,#d8dde2,#8a96a4 60%,#3a4252)"><h3>Financial Reporting</h3></div>
  <div class="btn abs" style="top:566px;left:511px"><span>View All Services</span><i style="color:#fff">★</i></div>
</section>

<section class="why abs" role="img" aria-label="Smiling property manager holding a tablet in front of a house">
  <div class="abs" style="left:-4px;top:-4px;width:30px;height:454px;background:var(--navy)"></div>
  <div class="panel abs">
    <div class="eyebrow">Why Choose Us</div>
    <div class="h2" style="margin:6px 0 18px">Why Choose Larkfield Ridge Management?</div>
    <ul>
      <li>Proven data-driven management strategies</li>
      <li>Faster response times</li>
      <li>Professional tenant communication</li>
      <li>Preventative maintenance approach</li>
      <li>Transparent financial reporting</li>
      <li>Focus on long-term property value</li>
    </ul>
  </div>
</section>

<section>
  <div class="abs center eyebrow" style="top:2686px">Gallery</div>
  <div class="abs center h2" style="top:2702px">Featured Properties</div>
  <div class="photo" role="img" aria-label="Aerial view of a hillside estate at sunset" style="left:0;top:2776px;width:268px;height:406px;background:linear-gradient(180deg,#c89a6a,#6a7a4a 55%,#3a4a2a)"></div>
  <div class="photo" role="img" aria-label="Waterfront residential community at sunrise" style="left:278px;top:2776px;width:607px;height:406px;border:5px solid var(--navy);background:linear-gradient(180deg,#e8b890,#9a8a7a 40%,#3a4a4a)">
    <div class="abs" style="left:0;right:0;bottom:0;height:90px;background:var(--navy);color:#fff;padding:18px 18px">
      <div style="font-size:19px">Residential Communities</div>
      <div style="font-size:10px;line-height:1.5;margin-top:4px;width:380px">Professional oversight, preventative maintenance, and consistent communication to keep communities running smoothly.</div>
      <div class="abs" style="right:20px;top:36px;font-size:22px">→</div>
    </div>
  </div>
  <div class="photo" role="img" aria-label="Apartment towers beside a road" style="left:895px;top:2776px;width:305px;height:406px;background:linear-gradient(180deg,#4a7ac8,#b8c8d8 55%,#6a8a4a)"></div>
  <div class="btn abs" style="top:3221px;left:459px"><span>View All Properties</span><i style="color:#fff">★</i></div>
</section>

<section class="faq abs">
  <div class="abs" style="left:24px;top:34px">
    <div class="eyebrow">FAQ</div>
    <div class="h2" style="color:#fff;margin-top:6px">Frequently Asked<br>Questions</div>
  </div>
  <div class="abs" style="left:24px;top:140px;width:390px;height:88px;background:#ece9e9;padding:14px 14px 0 30px;font-size:13px">
    <span class="abs" style="left:14px;top:20px;width:6px;height:6px;border-radius:50%;background:var(--navy)"></span>
    What types of properties do you manage?<span style="float:right">⌃</span>
    <p style="font-size:10px;color:var(--muted);margin-top:6px;line-height:1.5">We manage residential and investment properties with customized management solutions.</p>
  </div>
  <div class="q abs" style="top:246px">How do you screen tenants?<span>⌄</span></div>
  <div class="q abs" style="top:292px">How do you screen tenants?<span>⌄</span></div>
  <div class="q abs" style="top:338px">How do owners receive financial reports?<span>⌄</span></div>
  <div class="q abs" style="top:384px">How are maintenance requests handled?<span>⌄</span></div>
  <div class="photo" role="img" aria-label="Hand holding a wooden house model with a question mark" style="left:446px;top:8px;width:550px;height:438px;background:linear-gradient(135deg,#e8e0d0,#c08a50 55%,#6a5a4a)"></div>
</section>

<section>
  <div class="abs center eyebrow" style="top:3912px">Review</div>
  <div class="abs center h2" style="top:3928px">Trusted by Property Owners &amp; Tenants</div>
  <div class="arrow abs" style="left:40px;top:4072px">←</div>
  <div class="arrow abs" style="left:1122px;top:4072px">→</div>
  <div class="rev abs" style="left:93px"><div class="who"><span class="av"></span><div>Property Owner<div class="st">★★★★★</div></div></div><p>Larkfield Ridge Management has made owning rental properties stress-free. Their communication is excellent, maintenance is handled quickly, and I always know how my investment is performing.</p></div>
  <div class="rev abs" style="left:435px"><div class="who"><span class="av"></span><div>Residential Tenant<div class="st">★★★★★</div></div></div><p>From the leasing process to ongoing support, the entire experience has been smooth. The team is responsive, organized, and genuinely cares about both owners and tenants.</p></div>
  <div class="rev abs" style="left:779px"><div class="who"><span class="av"></span><div>Investment Property Owner<div class="st">★★★★★</div></div></div><p>Their proactive approach has reduced vacancies and kept our property in excellent condition. I highly recommend Larkfield Ridge Management to any real estate investor.</p></div>
</section>

<section>
  <div class="photo" role="img" aria-label="City skyline with residential blocks and a green hill" style="left:0;top:4216px;width:1200px;height:512px;background:linear-gradient(180deg,#dfe6ea,#a8a090 40%,#6a6a5a)"></div>
  <div class="abs" style="left:91px;top:4482px;width:1019px;height:216px;background:var(--red);color:#fff;text-align:center;padding-top:38px">
    <div style="font-size:30px;font-weight:500">Ready to Maximize Your Property Investment?</div>
    <p style="font-size:11px;line-height:1.6;margin-top:6px">Partner with Larkfield Ridge Management LLC for reliable, professional property management focused on protecting<br>your assets and improving tenant satisfaction.</p>
    <div class="btn light" style="margin-top:20px"><span>Request Your Free Consultation Today</span><i style="color:var(--red)">★</i></div>
  </div>
</section>

<footer class="foot">
  <div class="abs" style="left:92px;top:4776px;width:160px;color:var(--navy);font-weight:600;font-size:15px;line-height:1.2;display:flex;gap:8px;align-items:center"><span style="width:20px;height:20px;border-radius:50%;background:var(--red)"></span>LARKFIELD<br>RIDGE</div>
  <p class="abs" style="left:92px;top:4916px;width:200px;font-size:9px;color:var(--muted);line-height:1.6">Larkfield Ridge Management LLC delivers professional real estate and property management services built on proven systems, transparent communication, and data-driven strategies.</p>
  <div class="abs" style="left:92px;top:5002px;font-size:13px;display:flex;gap:8px;align-items:center">Follow us on <span style="width:22px;height:22px;border:1px solid #333;border-radius:50%"></span><span style="width:22px;height:22px;border:1px solid #333;border-radius:50%"></span></div>
  <div class="abs" style="left:344px;top:4748px;width:1px;height:280px;background:#ddd"></div>
  <div class="abs" style="left:600px;top:4748px;width:1px;height:280px;background:#ddd"></div>
  <div class="abs" style="left:862px;top:4748px;width:1px;height:280px;background:#ddd"></div>
  <div class="abs" style="left:362px;top:4770px"><h4>Main Links</h4><ul><li>Home</li><li>About Us</li><li>Services</li><li>Resources</li><li>FAQs</li><li>Contact Us</li></ul></div>
  <div class="abs" style="left:620px;top:4770px"><h4>Contact Us</h4>
    <ul><li style="display:flex;gap:8px;align-items:center"><svg width="18" height="18" viewBox="0 0 18 18"><circle cx="9" cy="9" r="8" fill="none" stroke="#333"/><rect x="5" y="6" width="8" height="6" fill="none" stroke="#333"/></svg>info@larkfieldridgemanagement.com</li>
    <li style="display:flex;gap:8px;align-items:center;margin-top:16px"><svg width="18" height="18" viewBox="0 0 18 18"><circle cx="9" cy="9" r="8" fill="none" stroke="#333"/><path d="M6 5c0 4 3 7 7 7l-1-2-2 1-3-3 1-2z" fill="#333"/></svg>555.014.2290</li></ul></div>
  <div class="abs" style="left:873px;top:4770px"><h4>Subscribe NewsLetter</h4>
    <div style="width:204px;height:36px;border:1px solid #bbb;font-size:10px;color:var(--muted);padding:11px 16px">Enter Your Email</div>
    <div class="btn" style="margin-top:14px"><span style="width:144px">Subscribe</span><i style="color:#fff">★</i></div></div>
  <div class="abs" style="left:873px;top:5010px;font-size:9px;color:var(--muted)">Privacy Policy | Cookie Policy | Terms and Conditions</div>
  <div class="abs" style="left:0;top:5040px;width:1200px;height:1px;background:#ddd"></div>
  <div class="abs center" style="top:5050px;font-size:9px;color:var(--muted)">© 2026 Larkfield Ridge Management LLC, All Rights Reserved.</div>
</footer>

</body>
</html>
```